Revamp our wedding venue website

Currently we are using wordpress for our website and hoped to find a designer that can assist us with making the website prettier and more pleasing and draw more interest. www.velmorhall.com is our current site. We are connected to google business mail, so I would prefer to stay with this for now and update our gallery with new photos, blog page and putting the contact us form back on all the pages.

Target Market(s)

20-40 years of age, all ranges of styles and generally clients looking for a different modern feel vs. a hotel hall.

Industry/Entity Type

Wedding

Logo Text

1927 Velmor Hall

Number of Pages Required

4 page

Font styles to use
Serif

Requirements
Must have
• Light, airy feel. Romantic and informative. Mobile friendly and easy to contact us-preferred contact form on all pages. Gallery of photos. Previous reviews
Nice to have
• Bio of staff, maybe some videos, and fun things to do in the area for out of town guests. Maps and also venue blank floor plan.

```html
<!DOCTYPE html>
<html lang="en">
<head>
<meta charset="utf-8">
<title>1927 Velmor Hall – Weddings &amp; Events</title>
<link href="https://fonts.googleapis.com/css2?family=Noto+Serif:ital,wght@0,400;0,700;1,400&family=Lobster&family=Dancing+Script:wght@500&family=Open+Sans:wght@400;600&display=swap" rel="stylesheet">
<style>
:root{
  --red:#c3161c;
  --red-dark:#a80f14;
  --ink:#444;
  --muted:#666;
  --heading:#747474;
  --rule:#cfcfcf;
  --footer:#3b3b3b;
  --footer-text:#d8d8d8;
  --white:#fff;
  --star:#f0a22b;
}
*{margin:0;padding:0;box-sizing:border-box}
html,body{width:723px;height:1200px;overflow:hidden;background:var(--white)}
body{position:relative;font-family:"Noto Serif",Georgia,serif;color:var(--ink)}
.abs{position:absolute}

/* header */
.tagline{left:60px;top:34px;font-size:8.5px;font-style:italic;color:var(--muted)}
.phone{left:60px;top:53px;display:flex;align-items:center;gap:6px;font-size:9px;font-style:italic;color:var(--muted)}
.phone .dot{width:17px;height:17px;border-radius:50%;background:var(--red);display:flex;align-items:center;justify-content:center}
.brand{left:262px;top:32px;width:200px;text-align:center;font-size:21px;color:#3a3a3a;line-height:1}
.social-label{left:470px;top:46px;width:84px;text-align:right;font-size:8px;font-style:italic;color:var(--muted);line-height:11px}
.social{left:565px;top:48px;display:flex;gap:4px}
.social span{width:16px;height:16px;border-radius:50%}

/* nav */
.nav{left:60px;top:104px;width:604px;display:flex}
.nav a{display:block;width:103px;text-decoration:none;border-left:1px dotted #bbb;padding-left:12px}
.nav a:first-child{border-left:none;padding-left:0}
.nav b{display:block;font-weight:400;font-size:8px;color:#333;letter-spacing:.2px}
.nav i{display:block;font-size:6.3px;color:#888;margin-top:2px}

/* hero */
.hero{left:60px;top:140px;width:604px;height:256px;background:linear-gradient(90deg,#4a4a2c 0%,#6d6a3c 30%,#e9e3da 48%,#d9cfc4 58%,#2b4d8f 72%,#39461f 100%)}
.hero-title{left:60px;top:230px;width:275px;text-align:center;color:var(--white);font-size:17px;letter-spacing:.5px}
.hero-sub{left:60px;top:256px;width:275px;text-align:center;color:var(--white);font-family:"Dancing Script",cursive;font-size:22px}
.btn{display:flex;align-items:center;justify-content:center;background:var(--red);color:var(--white);border-radius:14px;font-size:6.5px;letter-spacing:.2px;box-shadow:0 2px 0 var(--red-dark)}
.hero-btn{left:150px;top:295px;width:93px;height:23px}
.hero-dots{left:349px;top:382px;display:flex;gap:4px}
.hero-dots span{width:4px;height:4px;border-radius:50%;background:rgba(255,255,255,.6)}
.hero-dots span:first-child{background:var(--red)}

/* welcome */
.video{left:60px;top:430px;width:241px;height:165px;background:linear-gradient(160deg,#5d6a55 0%,#3a2a22 45%,#7a4a2c 100%)}
.video .play{position:absolute;left:107px;top:69px;width:27px;height:27px;border-radius:50%;background:rgba(255,255,255,.9)}
.video .bar{position:absolute;left:0;bottom:0;width:100%;height:17px;background:rgba(30,30,30,.85);display:flex;align-items:center;padding:0 4px;gap:4px}
.video .bar .pb{width:26px;height:13px;background:#222;border-radius:2px}
.video .bar .track{flex:1;height:5px;background:#4b5a5f;border-radius:2px}
.welcome-title{left:339px;top:426px;font-family:"Lobster",cursive;font-size:24px;color:var(--heading)}
.welcome-text{left:342px;top:465px;width:310px;font-size:7.4px;font-style:italic;line-height:15.5px;color:#555}
.contact-btn{left:342px;top:569px;width:93px;height:24px}

/* divider */
.divider{left:210px;top:624px;width:303px;height:8px}

/* recent events */
.section-title{left:0;width:723px;text-align:center;font-family:"Lobster",cursive;font-size:20px;color:var(--heading)}
.events-title{top:652px}
.events-sub{left:0;top:686px;width:723px;text-align:center;font-size:7.6px;font-style:italic;color:#555}
.event{width:122px;text-align:center}
.event .ring{width:122px;height:122px;border-radius:50%;border:1px solid #ddd;padding:5px;box-shadow:0 1px 3px rgba(0,0,0,.12)}
.event .photo{width:100%;height:100%;border-radius:50%}
.event p{margin-top:10px;font-size:6.6px;color:#333}
.arrow{width:15px;height:15px;border-radius:50%;border:1px solid #ccc;display:flex;align-items:center;justify-content:center}

/* testimonials */
.reviews-title{top:900px}
.review{width:290px;height:100px}
.review .avatar{position:absolute;left:0;top:0;width:74px;height:74px;border-radius:50%;border:4px solid #eee;box-shadow:0 1px 3px rgba(0,0,0,.15)}
.review .avatar div{width:100%;height:100%;border-radius:50%;background:radial-gradient(circle at 50% 45%,#d8b7a2 0%,#a9816b 55%,#efeae6 100%)}
.review .quote{position:absolute;left:95px;top:2px;width:170px;font-family:"Open Sans",sans-serif;font-style:italic;font-size:6.8px;line-height:13px;color:#444}
.review .qm{position:absolute;font-size:16px;color:#bbb;font-family:Georgia,serif}
.review .name{position:absolute;left:95px;top:55px;font-family:"Open Sans",sans-serif;font-size:6.6px;color:#333}
.review .name b{font-weight:600}
.review .name span{color:#888}
.review .stars{position:absolute;left:95px;top:66px;font-size:7px;color:var(--star);letter-spacing:.5px}

/* footer */
.footer{left:0;top:1073px;width:723px;height:127px;background:var(--footer)}
.footer-brand{left:262px;top:1093px;width:200px;text-align:center;font-size:18px;color:var(--white);line-height:1}
.footer-nav{left:0;top:1144px;width:723px;display:flex;justify-content:center;gap:23px;font-family:"Open Sans",sans-serif;font-size:8px;color:var(--footer-text)}
.footer-copy{left:0;top:1164px;width:723px;text-align:center;font-family:"Open Sans",sans-serif;font-size:7.6px;color:var(--footer-text)}
</style>
</head>
<body>

<header>
  <p class="abs tagline">Tampa's Most Unique Wedding and Events Venue</p>
  <div class="abs phone">
    <span class="dot"><svg width="9" height="9" viewBox="0 0 24 24"><path fill="#fff" d="M6.6 10.8a15 15 0 0 0 6.6 6.6l2.2-2.2c.3-.3.7-.4 1-.2 1.1.4 2.3.6 3.6.6.6 0 1 .4 1 1V20c0 .6-.4 1-1 1A17 17 0 0 1 3 4c0-.6.4-1 1-1h3.5c.6 0 1 .4 1 1 0 1.3.2 2.5.6 3.6.1.3 0 .7-.2 1z"/></svg></span>
    Call Us : 813.555.0142
  </div>
  <div class="abs brand">1927<br>Velmor Hall</div>
  <p class="abs social-label">Connect with<br>our social network :</p>
  <div class="abs social" aria-label="Social links">
    <span style="background:#2a64c5"></span>
    <span style="background:#3aa6e0"></span>
    <span style="background:#f0a22b"></span>
    <span style="background:#1f7cb0"></span>
    <span style="background:#d61f25"></span>
  </div>
</header>

<nav class="abs nav">
  <a href="#"><b>HOME</b><i>Welcome to our site</i></a>
  <a href="#"><b>WEDDINGS</b><i>View Wedding Events</i></a>
  <a href="#"><b>EVENTS</b><i>Book our services</i></a>
  <a href="#"><b>CATERING</b><i>Book you favorite</i></a>
  <a href="#"><b>GALLERY</b><i>View our photo gallery</i></a>
  <a href="#"><b>CONTACT US</b><i>Get in touch</i></a>
</nav>

<section>
  <div class="abs hero" role="img" aria-label="Photo of a bride in a white gown and a groom in a blue suit kissing her hand among trees"></div>
  <h1 class="abs hero-title" style="font-weight:400">WEDDINGS &amp; EVENTS</h1>
  <p class="abs hero-sub">at the 1927 Velmor Hall</p>
  <a class="abs btn hero-btn">VIEW OUR SERVICES</a>
  <div class="abs hero-dots"><span></span><span></span><span></span><span></span></div>
</section>

<section>
  <div class="abs video" role="img" aria-label="Video still of a model walking a runway at an evening event">
    <div class="play"><svg width="27" height="27" viewBox="0 0 27 27"><path d="M11.5 9.5l6 4-6 4z" fill="#333"/></svg></div>
    <div class="bar"><span class="pb"><svg width="26" height="13" viewBox="0 0 26 13"><path d="M11 3.5l5 3-5 3z" fill="#fff"/></svg></span><span class="track"></span></div>
  </div>
  <h2 class="abs welcome-title" style="font-weight:400">Welcome to 1927 Velmor Hall</h2>
  <p class="abs welcome-text">When choosing the location for your wedding or event, the 1927 Velmor Hall provides you with an all-inclusive experience, from the moment you arrive, through the creative food, and amazing photo opportunities. The unique open-kitchen provides you, and your guests a front-row seat to our creative, and talented chefs, as they prepare a culinary experience like no other. The full, and spacious bar, serves up wonderful libations and specialty cocktails that enhance your experience.</p>
  <a class="abs btn contact-btn">CONTACT HERE!</a>
</section>

<svg class="abs divider" viewBox="0 0 303 8" aria-hidden="true">
  <line x1="0" y1="3" x2="120" y2="3" stroke="#ccc"/><line x1="0" y1="5" x2="120" y2="5" stroke="#ccc"/>
  <line x1="183" y1="3" x2="303" y2="3" stroke="#ccc"/><line x1="183" y1="5" x2="303" y2="5" stroke="#ccc"/>
</svg>

<section>
  <h2 class="abs section-title events-title" style="font-weight:400">Recent Events</h2>
  <p class="abs events-sub">When choosing the location for your wedding or event, the 1927 Velmor Hall provides you with an all-inclusive experience</p>
  <div class="abs arrow" style="left:58px;top:773px"><svg width="6" height="8"><path d="M5 1L1 4l4 3" stroke="#bbb" fill="none"/></svg></div>
  <div class="abs event" style="left:84px;top:719px"><div class="ring"><div class="photo" role="img" aria-label="Group photo of guests at a corporate event" style="background:radial-gradient(circle,#b46a5a,#3a2a2e)"></div></div><p>CORPORATE EVENTS</p></div>
  <div class="abs event" style="left:228px;top:719px"><div class="ring"><div class="photo" role="img" aria-label="Banquet tables under blue and purple lighting" style="background:radial-gradient(circle,#c9b48c,#2a2c6a)"></div></div><p>PRIVATE EVENTS</p></div>
  <div class="abs event" style="left:372px;top:719px"><div class="ring"><div class="photo" role="img" aria-label="Crowd seated at a public event in the hall" style="background:radial-gradient(circle,#cfd2d6,#4a4d55)"></div></div><p>PUBLIC EVENTS</p></div>
  <div class="abs event" style="left:517px;top:719px"><div class="ring"><div class="photo" role="img" aria-label="Bride, groom and wedding party celebrating outdoors" style="background:radial-gradient(circle,#e8dcd4,#8a6f6a)"></div></div><p>WEDDING EVENTS</p></div>
  <div class="abs arrow" style="left:651px;top:773px"><svg width="6" height="8"><path d="M1 1l4 3-4 3" stroke="#bbb" fill="none"/></svg></div>
</section>

<section>
  <h2 class="abs section-title reviews-title" style="font-weight:400">What our client's say</h2>
  <div class="abs arrow" style="left:38px;top:981px"><svg width="6" height="8"><path d="M5 1L1 4l4 3" stroke="#bbb" fill="none"/></svg></div>
  <div class="abs review" style="left:70px;top:948px">
    <div class="avatar"><div role="img" aria-label="Portrait of a smiling bride"></div></div>
    <span class="qm" style="left:85px;top:-4px">“</span>
    <p class="quote">It's been almost a month since my wedding at the Velmor Hall and I am still with my mouth open, it was absolutely beautiful.</p>
    <span class="qm" style="left:268px;top:42px">”</span>
    <p class="name"><b>Marina &amp; Theo</b> <span>- Tampa, FL</span></p>
    <p class="stars">★★★★★</p>
  </div>
  <div class="abs review" style="left:375px;top:948px">
    <div class="avatar"><div role="img" aria-label="Portrait of a smiling bride"></div></div>
    <span class="qm" style="left:85px;top:-4px">“</span>
    <p class="quote">It's been almost a month since my wedding at the Velmor Hall and I am still with my mouth open, it was absolutely beautiful.</p>
    <span class="qm" style="left:268px;top:42px">”</span>
    <p class="name"><b>Marina &amp; Theo</b> <span>- Tampa, FL</span></p>
    <p class="stars">★★★★★</p>
  </div>
  <div class="abs arrow" style="left:668px;top:981px"><svg width="6" height="8"><path d="M1 1l4 3-4 3" stroke="#bbb" fill="none"/></svg></div>
</section>

<footer>
  <div class="abs footer"></div>
  <div class="abs footer-brand">1927<br>Velmor Hall</div>
  <div class="abs footer-nav"><span>Home</span><span>Weddings</span><span>Events</span><span>Catering</span><span>Gallery</span><span>Contact Us</span></div>
  <p class="abs footer-copy">© 2016. 1927 Velmor Hall. All rights reserved.</p>
</footer>

</body>
</html>
```